Business Cards Needed for Innovative Healthcare Marketing Company

We are a marketing company focused on healthcare. Our company is all about rebranding yourself renewing your image and generating results. The phoenix stands for "reborn" or "rising" which we provide new brands for our clients we take their old brands and renew it with creativity and innovation. I am looking for a business card with color dimension. I have attached an example of a card I think has the look and feel of what I am trying to accomplish. I like that the card example has black and grey font colors, I like the font placement and the small logo, I really like the use of the colors on the right those are the colors of my logo. My logo is phoenix so maybe incorporating flames similar to that design. I would like the back a solid color maybe red with an opaque version of the logo and website. As a marketing company I am always open to creative liberty!

Target Market(s)

Doctors and business professionals.

Industry/Entity Type

Marketing

Contact Information for Business Card

Valcorne Health Care Marketing
Marla Tenwick- CEO
#(512)638-2974
email-marla@valcorne.com
website- valcorne.com

Font styles to use
Sans Serif

Colors
ec1f27
f37122
ffc214
fbed22
fbf289
f04a50

Requirements
Must have
• The logo and required information
Nice to have
• icons by the information
Should not have
• child like font

```html
<!DOCTYPE html>
<html lang="en">
<head>
<meta charset="utf-8">
<title>Valcorne Health Care Marketing – Business Card</title>
<link rel="stylesheet" href="https://fonts.googleapis.com/css2?family=Open+Sans:wght@400;600;700&display=swap">
<style>
  :root {
    --canvas-bg: #e9e6e2;
    --card-white: #ffffff;
    --card-black: #0b0b0b;
    --brand-red: #a31f22;
    --brand-orange: #f4921f;
    --flame-orange: #f37122;
    --text-dark: #2a2a2a;
    --shadow: rgba(0, 0, 0, 0.22);
  }
  * { box-sizing: border-box; margin: 0; padding: 0; }
  html, body {
    width: 1200px;
    height: 900px;
    overflow: hidden;
    background: var(--canvas-bg);
    font-family: "Open Sans", Arial, sans-serif;
  }
  .canvas {
    position: relative;
    width: 1200px;
    height: 900px;
  }
  .card {
    position: absolute;
    top: 300px;
    width: 520px;
    height: 300px;
    border-radius: 4px;
    overflow: hidden;
    box-shadow: 0 10px 28px var(--shadow);
  }
  /* Back */
  .card-back {
    left: 50px;
    background: var(--card-black);
    display: flex;
    align-items: center;
    justify-content: center;
  }
  .card-back .brand-name {
    font-size: 40px;
    font-weight: 600;
    letter-spacing: 2px;
    color: var(--flame-orange);
    text-transform: uppercase;
  }
  /* Front */
  .card-front {
    left: 630px;
    background: var(--card-white);
  }
  .front-wave {
    position: absolute;
    inset: 0;
    width: 100%;
    height: 100%;
  }
  .holder {
    position: absolute;
    left: 48px;
    top: 58px;
  }
  .holder-name {
    font-size: 18px;
    font-weight: 700;
    color: var(--brand-red);
  }
  .holder-title {
    font-size: 14px;
    color: var(--text-dark);
    margin-top: 2px;
  }
  .brand {
    position: absolute;
    left: 250px;
    top: 52px;
    display: flex;
    align-items: center;
    gap: 10px;
  }
  .brand-dot {
    width: 16px;
    height: 16px;
    border-radius: 50%;
    background: var(--flame-orange);
    flex: none;
  }
  .brand .brand-name {
    font-size: 19px;
    font-weight: 400;
    color: var(--brand-red);
    line-height: 1.2;
    width: 230px;
  }
  .contact {
    position: absolute;
    left: 48px;
    top: 172px;
    list-style: none;
  }
  .contact li {
    display: flex;
    align-items: center;
    gap: 10px;
    font-size: 15px;
    color: var(--text-dark);
    line-height: 22px;
  }
  .contact svg { width: 12px; height: 12px; fill: var(--brand-red); flex: none; }
  .website {
    position: absolute;
    right: 26px;
    top: 192px;
    font-size: 12px;
    font-weight: 700;
    color: var(--card-white);
    white-space: nowrap;
  }
</style>
</head>
<body>
<main class="canvas">
  <section class="card card-back" aria-label="Card back">
    <span class="brand-name">Valcorne</span>
  </section>

  <section class="card card-front" aria-label="Card front">
    <svg class="front-wave" viewBox="0 0 520 300" preserveAspectRatio="none" aria-hidden="true">
      <path fill="var(--brand-orange)" d="M0,248 C150,250 290,214 392,152 C320,206 170,258 0,262 Z"/>
      <path fill="var(--brand-red)" d="M0,300 L0,270 C160,262 300,232 380,180 C430,148 480,130 520,124 L520,300 Z"/>
    </svg>

    <div class="holder">
      <p class="holder-name">Marla Tenwick</p>
      <p class="holder-title">CEO</p>
    </div>

    <div class="brand">
      <span class="brand-dot"></span>
      <span class="brand-name">Valcorne Health Care Marketing</span>
    </div>

    <ul class="contact">
      <li>
        <svg viewBox="0 0 12 12"><path d="M1 4c0-2 2-3 5-3s5 1 5 3l-1 1-2-1V3H4v1L2 5zM3 6h6l1 5H2z"/></svg>
        (512)638-2974
      </li>
      <li>
        <svg viewBox="0 0 12 12"><path d="M0 2h12v8H0zM1 3l5 4 5-4v-.2H1z" fill-rule="evenodd"/></svg>
        marla@valcorne.com
      </li>
    </ul>

    <p class="website">www.valcorne.com</p>
  </section>
</main>
</body>
</html>
```